Rack card 4"x9" for a construction company

We need to have a design for:
- the holder of rack cards. Letter size
- and the rack cards. Size 4"x9"

I attached a picture of the sample holder for example.

I am putting some of the brochures and pics we have in:

https://files.example-share.net/folders/7Qw3ZtR9pLx2MvB8nKd4YsH1cFj6GaUeT?usp=sharing

The Bodoni font is on the drive.
The rack card should call to action - to learn about our projects and that we are offering fixed price packages.

One of the sides of the rack card has to show our houses like we show on the website brindle-homes.ca
Images with short info like on the website http://www.brindle-homes.ca/our-projects/
Maybe have something like: Learn more about our recent projects at www...

You can use our logo from th pdf files. In the brochure on the cover page we show all the associations we are member of - this is a must to be shown.

Mentioning the website and the phone number is a must.

Bring your ideas.
Don't hesitate to ask questions.

Thanks
Marcus

```html
<!DOCTYPE html>
<html lang="en">
<head>
<meta charset="utf-8">
<title>Brindle Homes – Rack Card</title>
<link href="https://fonts.googleapis.com/css2?family=Bodoni+Moda:wght@500;700;800&family=Arimo:wght@400&display=swap" rel="stylesheet">
<style>
  :root{
    --navy:#101d40;
    --khaki:#8e8b6f;
    --khaki-light:#b3b08f;
    --green:#6cae5f;
    --panel-grey:#e7e7e7;
    --page:#eeeeee;
    --white:#ffffff;
    --ink:#2a2a2a;
    --photo-sky:#2c3f8c;
  }
  *{box-sizing:border-box;margin:0;padding:0}
  html,body{width:1200px;height:1200px;overflow:hidden;background:var(--page)}
  body{position:relative;font-family:"Arimo",Arial,sans-serif;color:var(--ink)}
  .serif{font-family:"Bodoni Moda","Times New Roman",serif}

  .card{position:absolute;top:57px;width:458px;height:1029px;background:var(--white);overflow:hidden;box-shadow:0 2px 10px rgba(0,0,0,.12)}
  .card--front{left:104px}
  .card--back{left:639px}

  .brand{display:flex;align-items:center;justify-content:center;gap:10px}
  .brand__mark{width:14px;height:14px;border-radius:50%;background:var(--navy)}
  .brand__name{font-family:"Bodoni Moda",serif;font-weight:700;font-size:30px;line-height:36px;letter-spacing:2px;color:var(--navy)}

  /* Front */
  .front__header{position:absolute;left:0;top:0;width:100%;height:136px;background:var(--panel-grey);display:flex;align-items:center;justify-content:center}
  .front__headline{position:absolute;top:148px;width:100%;text-align:center;font-weight:800;font-size:24.5px;line-height:28px;color:var(--navy);letter-spacing:.5px}

  .project{position:absolute;left:0;width:100%;height:155px}
  .project__photo{position:absolute;top:0;width:229px;height:155px}
  .project__cell{position:absolute;top:0;width:229px;height:155px}
  .project--info-left .project__cell{left:0}
  .project--info-left .project__photo{left:229px}
  .project--info-right .project__photo{left:0}
  .project--info-right .project__cell{left:229px}
  .project__box{position:absolute;left:16px;top:14px;width:213px;height:129px;border:1.5px solid #d3d1c2;padding:10px 0 0 12px}
  .project__title{font-family:"Bodoni Moda",serif;font-weight:700;font-size:16.5px;line-height:19px;color:var(--navy)}
  .project__rule{width:27px;height:1.5px;background:var(--khaki);margin:7px 0 12px}
  .project__stats{display:flex}
  .stat{width:65px;display:flex;flex-direction:column;align-items:flex-start}
  .stat:nth-child(2){padding-left:8px}
  .stat:nth-child(3){padding-left:6px}
  .stat svg{width:26px;height:18px}
  .stat__value{font-size:16.5px;line-height:19px;margin-top:8px;color:#333}

  .photo--dusk{background:linear-gradient(180deg,var(--photo-sky) 0%,#5a6488 55%,#6e7f63 100%)}
  .photo--day{background:linear-gradient(180deg,#a8c6e6 0%,#6e737b 55%,#5c7f48 100%)}
  .photo--stone{background:linear-gradient(180deg,#7a7f86 0%,#575d5c 60%,#6f9a54 100%)}

  .front__cta{position:absolute;left:0;top:859px;width:100%;height:170px;background:var(--navy);text-align:center}
  .front__cta-bump{position:absolute;left:50%;top:-12px;width:44px;height:44px;margin-left:-22px;border-radius:50%;background:var(--navy)}
  .front__cta p,.front__cta span{position:absolute;left:0;width:100%;text-align:center;font-family:"Bodoni Moda",serif;font-weight:700}
  .cta__line1{top:12px;font-size:25px;line-height:28px;letter-spacing:.5px;color:var(--white)}
  .cta__line2{top:40px;font-size:25px;line-height:28px;letter-spacing:.5px;color:var(--khaki)}
  .cta__visit{top:79px;font-size:16px;line-height:20px;color:var(--white)}
  .front__cta .cta__url{top:113px;left:42px;width:374px;height:36px;line-height:36px;border-radius:18px;background:linear-gradient(180deg,#9d9a7c,#6f6c53);font-size:21px;color:var(--white)}

  /* Back */
  .back__hero{position:absolute;left:0;top:0;width:100%;height:259px;background:linear-gradient(180deg,#2440a8 0%,#4c5c99 40%,#b9b9b7 75%,#5f8d46 100%)}
  .back__interiors{position:absolute;left:0;top:259px;width:100%;height:146px;display:flex}
  .back__interiors div{flex:1}
  .interior--kitchen{background:linear-gradient(180deg,#d8d4cc,#ebe8e2)}
  .interior--living{background:linear-gradient(180deg,#6b6b6e,#d9d6d0)}
  .back__headline{position:absolute;top:413px;width:100%;text-align:center;font-family:"Bodoni Moda",serif;font-weight:800;font-size:30px;line-height:34px;letter-spacing:.5px;color:var(--navy)}
  .back__headline span{color:var(--green);display:block}
  .back__copy{position:absolute;left:22px;top:491px;width:414px;text-align:center;font-size:14.6px;line-height:19.2px;color:#3b3b3b}
  .back__members-title{position:absolute;top:589px;width:100%;text-align:center;font-family:"Bodoni Moda",serif;font-weight:700;font-size:15px;line-height:18px;letter-spacing:.8px;color:var(--navy)}
  .badges{position:absolute;top:628px;left:22px;width:414px;display:flex;justify-content:space-between;align-items:center}
  .badge{width:64px;height:50px;border-radius:6px;background:#d7dbe0}
  .badge--round{border-radius:50%;width:54px;height:54px;background:#c9d6e8}
  .badge--red{background:#e6c9c9}
  .badge--green{background:#cfe1cc}
  .badge--wide{width:108px;height:38px;background:#2c5f96}

  .back__footer{position:absolute;left:0;top:721px;width:100%;height:308px;background:var(--panel-grey)}
  .back__footer-bump{position:absolute;left:50%;top:-15px;width:44px;height:44px;margin-left:-22px;border-radius:50%;background:var(--panel-grey)}
  .back__footer .brand{position:absolute;top:98px;width:100%}
  .contact-icons{position:absolute;top:150px;width:100%;display:flex;justify-content:center;gap:18px}
  .contact-icons svg{width:35px;height:35px}
  .contact-list{position:absolute;top:198px;width:100%;text-align:center;font-size:17.5px;line-height:24px;color:#222;font-style:normal}
</style>
</head>
<body>

<section class="card card--front">
  <header class="front__header">
    <div class="brand"><span class="brand__mark"></span><span class="brand__name">BRINDLE HOMES</span></div>
  </header>
  <h1 class="front__headline serif">BUILD THE HOME OF YOUR<br>DREAMS IN VANCOUVER</h1>

  <svg width="0" height="0" style="position:absolute">
    <defs>
      <symbol id="icon-bed" viewBox="0 0 26 18"><rect x="1" y="4" width="2.5" height="13" fill="#9a977b"/><rect x="1" y="10" width="24" height="4" fill="#9a977b"/><rect x="4" y="7" width="6" height="3" fill="#9a977b"/><rect x="22.5" y="10" width="2.5" height="7" fill="#9a977b"/></symbol>
      <symbol id="icon-bath" viewBox="0 0 26 18"><path d="M3 9h20v2a5 5 0 0 1-5 5H8a5 5 0 0 1-5-5z" fill="#9a977b"/><path d="M17 9V3h4v2" stroke="#9a977b" stroke-width="1.5" fill="none"/><rect x="7" y="16" width="2" height="2" fill="#9a977b"/><rect x="17" y="16" width="2" height="2" fill="#9a977b"/></symbol>
      <symbol id="icon-area" viewBox="0 0 26 18"><path d="M4 16 L20 2 V16 Z" fill="none" stroke="#9a977b" stroke-width="1.8"/><path d="M9 13h8V6" fill="none" stroke="#9a977b" stroke-width="1.2"/></symbol>
    </defs>
  </svg>

  <article class="project project--info-left" style="top:220px">
    <div class="project__cell"><div class="project__box">
      <h2 class="project__title">Renfrew<br>Traditional Craftsman</h2>
      <div class="project__rule"></div>
      <div class="project__stats">
        <div class="stat"><svg><use href="#icon-bed"/></svg><span class="stat__value">7</span></div>
        <div class="stat"><svg><use href="#icon-bath"/></svg><span class="stat__value">5</span></div>
        <div class="stat"><svg><use href="#icon-area"/></svg><span class="stat__value">2,679</span></div>
      </div>
    </div></div>
    <div class="project__photo photo--day" role="img" aria-label="Photo of a dark-sided three-storey craftsman house under a blue sky"></div>
  </article>

  <article class="project project--info-right" style="top:375px">
    <div class="project__photo photo--stone" role="img" aria-label="Photo of a stone and shingle craftsman home with landscaped front garden"></div>
    <div class="project__cell"><div class="project__box">
      <h2 class="project__title">Burnaby<br>Modern Craftsman</h2>
      <div class="project__rule"></div>
      <div class="project__stats">
        <div class="stat"><svg><use href="#icon-bed"/></svg><span class="stat__value">8</span></div>
        <div class="stat"><svg><use href="#icon-bath"/></svg><span class="stat__value">8</span></div>
        <div class="stat"><svg><use href="#icon-area"/></svg><span class="stat__value">4,740</span></div>
      </div>
    </div></div>
  </article>

  <article class="project project--info-left" style="top:530px">
    <div class="project__cell"><div class="project__box">
      <h2 class="project__title">Renfrew<br>Modern Craftsman</h2>
      <div class="project__rule"></div>
      <div class="project__stats">
        <div class="stat"><svg><use href="#icon-bed"/></svg><span class="stat__value">9</span></div>
        <div class="stat"><svg><use href="#icon-bath"/></svg><span class="stat__value">7</span></div>
        <div class="stat"><svg><use href="#icon-area"/></svg><span class="stat__value">3,637</span></div>
      </div>
    </div></div>
    <div class="project__photo photo--dusk" role="img" aria-label="Dusk photo of a grey modern craftsman home with lit eaves"></div>
  </article>

  <article class="project project--info-right" style="top:684px">
    <div class="project__photo photo--dusk" role="img" aria-label="Dusk photo of a white luxury home with front stairs and lawn"></div>
    <div class="project__cell"><div class="project__box">
      <h2 class="project__title">Kerrisdale<br>Modern Opulence</h2>
      <div class="project__rule"></div>
      <div class="project__stats">
        <div class="stat"><svg><use href="#icon-bed"/></svg><span class="stat__value">4</span></div>
        <div class="stat"><svg><use href="#icon-bath"/></svg><span class="stat__value">6</span></div>
        <div class="stat"><svg><use href="#icon-area"/></svg><span class="stat__value">3,242</span></div>
      </div>
    </div></div>
  </article>

  <footer class="front__cta">
    <div class="front__cta-bump"></div>
    <p class="cta__line1">LEARN MORE ABOUT</p>
    <p class="cta__line2">OUR RECENT PROJECTS</p>
    <p class="cta__visit">Visit Us At</p>
    <span class="cta__url">www.brindle-homes.ca</span>
  </footer>
</section>

<section class="card card--back">
  <div class="back__hero" role="img" aria-label="Dusk photo of a white luxury home with lit windows and stone steps"></div>
  <div class="back__interiors">
    <div class="interior--kitchen" role="img" aria-label="Photo of a bright kitchen and living room"></div>
    <div class="interior--living" role="img" aria-label="Photo of a living room with stone fireplace"></div>
  </div>
  <h2 class="back__headline">MAKING YOUR DREAM<span>HOME A REALITY.</span></h2>
  <p class="back__copy">If you want the home of your dreams to move seamlessly from vision to reality, it’s vital that you partner with a builder with the ability – and the capacity – to guide you through each step of the building process.</p>
  <h3 class="back__members-title">PROUD MEMBERS OF</h3>
  <div class="badges">
    <span class="badge badge--round"></span>
    <span class="badge badge--red"></span>
    <span class="badge badge--green"></span>
    <span class="badge"></span>
    <span class="badge badge--wide"></span>
  </div>

  <footer class="back__footer">
    <div class="back__footer-bump"></div>
    <div class="brand"><span class="brand__mark"></span><span class="brand__name">BRINDLE HOMES</span></div>
    <div class="contact-icons">
      <svg viewBox="0 0 36 36"><circle cx="18" cy="18" r="16.5" fill="none" stroke="var(--green)" stroke-width="2"/><path d="M18 8a6 6 0 0 1 6 6c0 5-6 12-6 12s-6-7-6-12a6 6 0 0 1 6-6z" fill="var(--green)"/><circle cx="18" cy="14" r="2.2" fill="var(--panel-grey)"/></svg>
      <svg viewBox="0 0 36 36"><circle cx="18" cy="18" r="16.5" fill="none" stroke="var(--green)" stroke-width="2"/><path d="M16 10c-3 2-3 14 0 16l2-1-1-5-1.5 .5c-.8-2-.8-4 0-6L17 15l1-5z" fill="var(--green)"/></svg>
      <svg viewBox="0 0 36 36"><circle cx="18" cy="18" r="16.5" fill="none" stroke="var(--green)" stroke-width="2"/><rect x="10" y="12" width="16" height="12" rx="1" fill="var(--green)"/><path d="M10 13l8 6 8-6" fill="none" stroke="var(--panel-grey)" stroke-width="1.5"/></svg>
      <svg viewBox="0 0 36 36"><circle cx="18" cy="18" r="16.5" fill="none" stroke="var(--green)" stroke-width="2"/><g fill="none" stroke="var(--green)" stroke-width="1.5"><circle cx="18" cy="18" r="9"/><ellipse cx="18" cy="18" rx="4" ry="9"/><path d="M9 18h18M10.5 13.5h15M10.5 22.5h15"/></g></svg>
    </div>
    <address class="contact-list">
      208-915 Alder Lane, Vancouver, BC, V6B 1K7<br>
      604.555.0187<br>
      contact@brindle-homes.ca<br>
      www.brindle-homes.ca
    </address>
  </footer>
</section>

</body>
</html>
```